New Business card design to reflect rebrand

I would like a business card design with a good base colour for our new logo and also a placeholder for a profile pic of the card holder. the design needs to be editable to the point that we can easily change the picture of the person and use that design for printmerlo etc. we are looking at a metalic finish business card so will need a good base colour to bring out the finish.

Target Market(s)

prospective customers

Industry/Entity Type

Business

Contact Information for Business Card

I would like one editable design that we can change the name of the card holder and profile picture. The design need to be in a format that be send to printmerlo etc.

Our address is Fenwick Lodge, Copse Lane, Ashcombe Vale, GU14 3TP Tel no. 01483 556172

Requirements
Must have
• place holder for a profile pic for the card holder. in AI or preferably PSD format

```html
<!DOCTYPE html>
<html lang="en">
<head>
<meta charset="utf-8">
<title>Halden Workplace Services – Business Card</title>
<link rel="stylesheet" href="https://fonts.googleapis.com/css2?family=Montserrat:wght@600&family=Roboto+Condensed:wght@400;700&display=swap">
<style>
  :root {
    --stage: #2a2a2a;
    --slate: #42566f;
    --orange: #ee6410;
    --white: #ffffff;
    --photo-bg: #dcdcdc;
    --photo-figure: #9a9a9a;
  }
  * { box-sizing: border-box; margin: 0; padding: 0; }
  html, body { width: 1200px; height: 987px; overflow: hidden; }
  body {
    background: var(--stage);
    position: relative;
    font-family: "Roboto Condensed", "Arial Narrow", sans-serif;
  }
  .card {
    position: absolute;
    left: 293px;
    width: 615px;
    height: 352px;
    overflow: hidden;
    box-shadow: 0 6px 18px rgba(0,0,0,.55);
  }
  .card--front { top: 130px; background: var(--white); }
  .card--back  { top: 505px; background: var(--slate); }

  .front-bands { position: absolute; inset: 0; }

  .brand { position: absolute; font-family: "Montserrat", sans-serif; font-weight: 600; }
  .brand__mark { display: inline-block; width: 26px; height: 26px; margin-bottom: 10px; background: var(--orange); }
  .brand__name { display: block; line-height: 1; }
  .brand__name--main { font-size: 40px; letter-spacing: 1px; }
  .brand__name--sub { font-size: 16.5px; letter-spacing: 2.6px; margin-top: 6px; }

  .card--front .brand { left: 40px; top: 62px; color: var(--slate); }
  .card--back .brand { left: 0; right: 0; top: 112px; text-align: center; color: var(--white); }

  .profile-photo {
    position: absolute;
    left: 443px; top: 84px;
    width: 123px; height: 153px;
    border-radius: 6px;
    background: linear-gradient(180deg, var(--photo-bg) 0%, var(--photo-figure) 100%);
  }

  .address {
    position: absolute;
    left: 37px; top: 249px;
    color: var(--white);
    font-size: 16px;
    font-style: normal;
    line-height: 23px;
  }
  .address__tel { margin-top: 3px; }

  .holder {
    position: absolute;
    left: 420px; width: 170px; top: 256px;
    text-align: center;
  }
  .holder__name { color: var(--orange); font-weight: 700; font-size: 22px; letter-spacing: .5px; }
  .holder__title { color: var(--white); font-size: 16px; margin-top: 4px; }
</style>
</head>
<body>

<section class="card card--front">
  <svg class="front-bands" width="615" height="352" viewBox="0 0 615 352" aria-hidden="true">
    <path d="M0 210 H342 Q354 210 364 200 H0 Z" fill="var(--orange)"/>
    <path d="M0 214 H342 Q360 214 372 202 Q385 190 405 190 H615 V352 H0 Z" fill="var(--slate)"/>
  </svg>

  <div class="brand">
    <span class="brand__mark"></span>
    <span class="brand__name brand__name--main">HALDEN</span>
    <span class="brand__name brand__name--sub">WORKPLACE SERVICES</span>
  </div>

  <div class="profile-photo" role="img" aria-label="Profile photo of the card holder"></div>

  <address class="address">
    <div>Fenwick Lodge</div>
    <div>Copse Lane, Ashcombe Vale, GU14 3TP</div>
    <div class="address__tel">Tel : 01483 556172</div>
  </address>

  <div class="holder">
    <div class="holder__name">OWEN MERCER</div>
    <div class="holder__title">CEO/FOUNDER</div>
  </div>
</section>

<section class="card card--back">
  <div class="brand">
    <span class="brand__mark"></span>
    <span class="brand__name brand__name--main">HALDEN</span>
    <span class="brand__name brand__name--sub">WORKPLACE SERVICES</span>
  </div>
</section>

</body>
</html>
```